ASSET BASED PROGRAM FLIER

Need flier to market hard money loan products offered HARD MONEY FIX & FLIP PROGRAMS

We offer a variety of loan programs Some program highlights include......

1) No Minimum Credit Score
2) 3-5 Day Close
3) Up to 100% of Purchase & Rehab
4) Rates as Low as 7%
5) Loans Offered Nationwide

Contact us today for more information at (800) 416-9052 x23 or email us at mbelcourt@quillmarkfunding.com NMLS #318746 www.quillmarkfunding.com

Industry/Entity Type

Loan

```html
<!DOCTYPE html>
<html lang="en">
<head>
<meta charset="utf-8">
<title>Hard Money Fix &amp; Flip Programs – Quillmark Funding</title>
<link rel="stylesheet" href="https://fonts.googleapis.com/css2?family=Cinzel:wght@400;700&family=Lato:wght@400;700&family=Roboto+Condensed:wght@400;700&display=swap">
<style>
  :root {
    --bg: #e9e9e9;
    --paper: #ffffff;
    --blue: #0d5eb0;
    --blue-deep: #0a4f9c;
    --blue-light: #1778cf;
    --gold: #b19a2c;
    --gold-light: #c6b24a;
    --ink: #1c1c1c;
    --text: #333333;
  }
  * { box-sizing: border-box; margin: 0; padding: 0; }
  html, body { width: 1200px; height: 1200px; overflow: hidden; background: var(--bg); }
  .flyer {
    position: absolute; left: 172px; top: 0;
    width: 856px; height: 1200px;
    background: linear-gradient(#fff 55%, #f1f1f1 75%, #fff);
    overflow: hidden;
  }
  .flyer-art { position: absolute; inset: 0; }
  .hero-photo {
    position: absolute; inset: 0;
    background: linear-gradient(135deg, #f1f2ee 0%, #d9dfe0 55%, #9aa3ad 100%);
    clip-path: path('M0 0H856V383C640 380 460 360 330 330 200 290 80 220 0 185Z');
  }
  .brand-seal {
    position: absolute; left: 73px; top: 197px;
    width: 270px; height: 270px; border-radius: 50%;
    background: var(--paper); border: 6px solid var(--blue);
    display: flex; align-items: center; justify-content: center;
  }
  .brand-name {
    font-family: "Lato", sans-serif; font-weight: 700;
    font-size: 27px; color: var(--blue); text-align: center; line-height: 1.15;
  }
  .headline {
    position: absolute; left: 0; width: 100%; top: 498px;
    text-align: center; font-family: "Cinzel", serif; font-weight: 400;
    font-size: 58px; color: var(--blue); letter-spacing: 1px; padding-left: 130px;
  }
  .headline-band {
    position: absolute; left: 147px; top: 582px; width: 562px; height: 71px;
    background: linear-gradient(var(--gold-light), var(--gold));
    border-radius: 10px; box-shadow: 0 14px 16px -10px rgba(0,0,0,.3);
    display: flex; align-items: center; justify-content: center;
    font-family: "Cinzel", serif; font-weight: 700; font-size: 58px; color: var(--ink);
  }
  .intro {
    position: absolute; left: 60px; top: 726px;
    font-family: "Roboto Condensed", sans-serif; font-size: 21px; color: var(--text); line-height: 28px;
  }
  .intro strong { color: var(--blue); font-weight: 700; display: flex; align-items: center; gap: 14px; }
  .intro strong::after { content: ""; width: 130px; height: 1px; background: var(--text); margin-top: 8px; }
  .highlights {
    position: absolute; left: 452px; top: 704px; list-style: none;
    font-family: "Lato", sans-serif; font-size: 19px; color: var(--text); line-height: 23.5px;
  }
  .highlights li::before { content: "•"; color: var(--blue); margin-right: 12px; }
  .highlights b { color: var(--blue); }
  .crew-photo {
    position: absolute; left: 520px; top: 830px; width: 336px; height: 370px;
    background: linear-gradient(180deg, rgba(225,215,200,.55) 0%, #c9a58c 45%, #9c5a5c 80%, #7a3e4a 100%);
  }
  .contact {
    position: absolute; left: 48px; top: 968px; list-style: none;
    font-family: "Lato", sans-serif; color: #fff;
  }
  .contact li { display: flex; align-items: center; gap: 14px; font-size: 16.5px; height: 33px; }
  .contact li.phone { font-size: 27px; height: 42px; }
  .contact svg { width: 18px; height: 18px; flex: none; }
  .social { position: absolute; left: 44px; top: 1113px; display: flex; gap: 17px; }
  .social span { width: 33px; height: 33px; border-radius: 50%; background: var(--gold); }
</style>
</head>
<body>
<main class="flyer">
  <div class="hero-photo" role="img" aria-label="Photo of a bright renovated kitchen interior with a builder and a businesswoman reviewing a clipboard"></div>
  <svg class="flyer-art" viewBox="0 0 856 1200" aria-hidden="true">
    <defs>
      <linearGradient id="footBlue" x1="0" y1="0" x2="0" y2="1">
        <stop offset="0" stop-color="#1778cf"/><stop offset="1" stop-color="#0a4f9c"/>
      </linearGradient>
    </defs>
    <path d="M0 185C80 220 200 290 330 330 460 362 640 385 856 383V395C640 402 450 385 320 350 190 312 80 250 0 220Z" fill="var(--blue)"/>
    <path d="M0 915C250 895 470 900 660 990 470 945 250 935 0 945Z" fill="var(--gold)"/>
    <path d="M0 948C250 930 470 940 660 1000L856 1060V1200H0Z" fill="url(#footBlue)"/>
  </svg>

  <div class="brand-seal"><span class="brand-name">Quillmark<br>Funding</span></div>

  <h1 class="headline">HARD MONEY FIX &amp;</h1>
  <div class="headline-band">FLIP PROGRAMS</div>

  <p class="intro">We offer a variety of<br>loan programs Some program<br><strong>HIGHLIGHTS INCLUDE</strong></p>
  <ul class="highlights">
    <li>No Minimum Credit Score</li>
    <li>3-5 Day Close</li>
    <li>Up to <b>100%</b> of Purchase &amp; Rehab</li>
    <li>Rates as Low as <b>7%</b></li>
    <li>Loans Offered Nationwide</li>
  </ul>

  <div class="crew-photo" role="img" aria-label="Photo of a smiling contractor in a hard hat and plaid shirt carrying lumber"></div>

  <ul class="contact">
    <li class="phone"><svg viewBox="0 0 24 24"><path fill="#fff" d="M6.6 10.8a15 15 0 0 0 6.6 6.6l2.2-2.2c.3-.3.7-.4 1-.2 1.1.4 2.300.6 3.6.6.6 0 1 .4 1 1V20c0 .6-.4 1-1 1A17 17 0 0 1 3 4c0-.6.4-1 1-1h3.5c.6 0 1 .4 1 1 0 1.3.2 2.5.6 3.6.1.3 0 .7-.2 1z"/></svg>(800) 416-9052 x23</li>
    <li><svg viewBox="0 0 24 24"><path fill="#fff" d="M3 6h18v12H3z"/><path d="M3 6l9 7 9-7" stroke="#0d5eb0" stroke-width="2" fill="none"/></svg>mbelcourt@quillmarkfunding.com</li>
    <li><svg viewBox="0 0 24 24"><rect x="5" y="3" width="14" height="18" fill="none" stroke="#fff" stroke-width="2"/><path d="M8 8h8M8 12h8M8 16h5" stroke="#fff" stroke-width="2"/></svg>NMLS #318746</li>
    <li><svg viewBox="0 0 24 24"><circle cx="12" cy="12" r="9" fill="none" stroke="#fff" stroke-width="2"/><path d="M3 12h18M12 3c3 3 3 15 0 18M12 3c-3 3-3 15 0 18" fill="none" stroke="#fff" stroke-width="1.5"/></svg>www.quillmarkfunding.com</li>
  </ul>
  <div class="social" aria-hidden="true"><span></span><span></span><span></span></div>
</main>
</body>
</html>
```